Very new and innovative Web design for Property managers of Vacation rentals

We are looking for a new website design for travel agencies and property managers specialised on vacation rentals business, holiday villas and apartments.

The end users of this website are travellers who are looking for a vacation home for their next holiday: this is the reason why the website must be easy to use, attractive, professional, possibly elegant and focused on get new reservations.

This is a draft of our current website: https://intro3.kelumsito.com/
Please consider that we would like to have proposals with a totally different and innovative layout, surprise us!

These are the pages of the website:
• Homepage: feel free to redesign all the homepage as you wish, surprise us with something very new! Please consider that Property manager/Travel agencies usually want to have the opportunity to put in evidence groups of houses with specific characteristics (eg. villas with private swimming pool, apartment in big/small towns, villas with air co, etc…), destinations and tourist areas, and sometimes experiences or activities (please consider that the website layout must be suitable even if some of the previous sections are not used).
• Search page: we’d like to organise the results of the search page in three different ways:
o Grid
o Map
o List
• Property page: to illustrate the characteristics, descriptions, images, …. of the property. It is very important to put in evidence images of the property and to maintain the booking form (and the other call to action bottom – eg. whatsapp) always visible
• Custom pages: static pages composed usually by text, images and call to actions
• Contact us (general form)
• Info request (specific of a property form)
• Booking process
• Blog, organised in four pages:
o Home Page – introduction to the blog
o List of articles
o Single article
o Site Map (presentation of categories and sub-categories)

If possible, we’d prefer to receive the material in Adobe XD or similar so that we can obtain the three versions:
- smartphone
- tablet
- desktop

The website will be then developed in Bootstrap: as a result we’ll need the icons in SVG format (or the library used)

In attachment you can find the map of the website pages

```html
<!DOCTYPE html>
<html lang="en">
<head>
<meta charset="utf-8">
<title>StayNest – Contact page, desktop and mobile</title>
<link rel="stylesheet" href="https://fonts.googleapis.com/css2?family=Libre+Caslon+Text&family=Montserrat:wght@400;500;600&family=Playfair+Display:wght@700&display=swap">
<style>
:root{
  --green:#14b57e;
  --stage:#5f7d71;
  --ink:#2a2a2a;
  --muted:#6f6f6f;
  --line:#cfd4d2;
  --footer:#1d1d1d;
  --footer-text:#b9b9b9;
  --white:#ffffff;
}
*{box-sizing:border-box;margin:0;padding:0}
html,body{width:884px;height:1200px;overflow:hidden}
body{background:var(--stage);font-family:"Montserrat",sans-serif;color:var(--ink);position:relative}
.brand{position:absolute;display:flex;align-items:center;gap:6px;font-family:"Montserrat",sans-serif;font-weight:500;color:var(--ink);white-space:nowrap}
.brand .mark{background:var(--green);flex:none}
.brand--stage{left:100px;top:40px;font-size:34px;color:var(--white)}
.brand--stage .mark{width:30px;height:30px}
.side-label{position:absolute;font-family:"Playfair Display",serif;font-weight:700;color:var(--white);white-space:nowrap;font-size:74px;line-height:1}
.side-label--desktop{left:22px;top:1175px;transform:rotate(-90deg);transform-origin:0 0}
.side-label--mobile{left:860px;top:385px;transform:rotate(90deg);transform-origin:0 0}

.page{position:absolute;background:var(--white);overflow:hidden;transform-origin:0 0}
.page *{position:absolute}
.page .brand{position:absolute}
.desk{left:140px;top:165px;width:652px;height:1015px;transform:scale(.7)}
.mob{left:640px;top:130px;width:214px;height:1590px;transform:scale(.66)}

.topbar{background:var(--green);color:var(--white);font-size:6px;font-weight:600;display:flex;align-items:center;gap:12px;padding-left:30px}
.topbar span{position:static}
.nav{font-size:7px;color:#444;display:flex;gap:30px}
.nav span{position:static}
.nav .on{color:var(--green);font-weight:600}
.hero{background:linear-gradient(90deg,#2f2b36 0%,#6a573f 18%,#3c3a48 36%,#7d6a52 52%,#2b3145 68%,#6e5d47 84%,#363340 100%)}
.hero-title{font-family:"Libre Caslon Text",serif;color:var(--white);text-align:center;width:100%;letter-spacing:.5px}
.crumb{font-size:6px;color:var(--muted)}
.crumb b{position:static;font-weight:400;color:var(--ink)}
.h1{font-family:"Libre Caslon Text",serif;color:var(--ink)}
.lead{color:var(--muted);line-height:1.75}
.h2{font-family:"Libre Caslon Text",serif;color:var(--ink)}
.info{display:flex;gap:6px;color:var(--ink);line-height:1.6}
.info svg{position:static;flex:none;margin-top:1px}
.info span{position:static}
.field{border:1px solid var(--line);color:#8a8a8a;padding:0 7px;display:flex;align-items:center}
.field--area{align-items:flex-start;padding-top:7px}
.check{border:1px solid var(--line);background:var(--white)}
.optin{color:var(--muted)}
.verify{border:1px solid #d7d7d7;background:#f9f9f9;box-shadow:0 1px 2px rgba(0,0,0,.12)}
.send{background:var(--green);color:var(--white);font-weight:600;display:flex;align-items:center;justify-content:center}
.map{background:linear-gradient(160deg,#eef1f3 0%,#e6eaed 55%,#dfe6ea 100%)}
.footer{background:var(--footer);color:var(--footer-text)}
.footer .brand{color:var(--white)}
.f-head{font-family:"Libre Caslon Text",serif;color:var(--white)}
.f-list{display:flex;flex-direction:column}
.f-list span{position:static}
.f-row{display:flex;align-items:flex-start;gap:5px}
.f-row svg,.f-row span{position:static;flex:none}
.dot{border-radius:50%;background:var(--white)}
.copy{text-align:center;width:100%}
.copy b{position:static;color:var(--white);font-weight:500}
</style>
</head>
<body>

<div class="brand brand--stage"><span class="mark"></span>StayNest</div>
<div class="side-label side-label--desktop">Desktop Version</div>
<div class="side-label side-label--mobile">Mobile Version</div>

<!-- Desktop page -->
<section class="page desk" aria-label="Contact page, desktop layout">
  <div class="topbar" style="left:440px;top:0;width:212px;height:22px">
    <span>&#9786; LOGIN</span><span>&#9825; WHISHLIST</span><span>EN &#709;</span>
  </div>
  <div class="brand" style="left:60px;top:16px;font-size:17px"><span class="mark" style="width:16px;height:16px"></span>StayNest</div>
  <nav class="nav" style="left:310px;top:34px">
    <span>HOME</span><span>SEARCH</span><span>PROPERTY</span><span>CUSTOM</span><span class="on">CONTACT US</span>
  </nav>
  <div class="hero" role="img" aria-label="Photo of an arcaded shopping street with lanterns and a small bridge" style="left:0;top:50px;width:652px;height:156px"></div>
  <div class="hero-title" style="left:0;top:114px;font-size:24px">CONTACT US</div>

  <div class="crumb" style="left:60px;top:224px">Home &nbsp;/&nbsp; <b>Contact Us</b></div>
  <div class="h1" style="left:60px;top:252px;font-size:24px">Contact Us</div>
  <p class="lead" style="left:60px;top:283px;width:370px;font-size:7px">Use this form to contact us regarding any topics other than specific property requests which should be done using the form on the property detail pages.</p>

  <div class="h2" style="left:61px;top:319px;font-size:12.5px">StayNest</div>
  <div class="info" style="left:60px;top:350px;font-size:7px;width:160px">
    <svg width="7" height="9" viewBox="0 0 10 13"><path d="M5 0a5 5 0 0 1 5 5c0 3.5-5 8-5 8S0 8.5 0 5a5 5 0 0 1 5-5z" fill="#14b57e"/><circle cx="5" cy="5" r="1.8" fill="#fff"/></svg>
    <span>Via degli Orti 7 50100 Valdarno,<br>Toscana, Italy</span>
  </div>
  <div class="info" style="left:60px;top:384px;font-size:7px">
    <svg width="7" height="8" viewBox="0 0 10 10"><path d="M2 0l2 2.5-1.2 1.3a6 6 0 0 0 3.4 3.4L7.5 6 10 8l-1.5 2C4 10 0 6 0 1.5z" fill="#14b57e"/></svg>
    <span>Phone: +39 055 4128370</span>
  </div>
  <div class="info" style="left:60px;top:407px;font-size:7px">
    <svg width="7" height="8" viewBox="0 0 10 10"><rect x="0" y="3" width="10" height="7" fill="#14b57e"/><rect x="2" y="0" width="6" height="4" fill="#14b57e"/></svg>
    <span>Fax: +39 055 4128371</span>
  </div>
  <div class="info" style="left:60px;top:431px;font-size:7px">
    <svg width="7" height="8" viewBox="0 0 10 10"><circle cx="5" cy="5" r="4.5" fill="#14b57e"/></svg>
    <span>VAT Code: IT04217650392</span>
  </div>

  <div class="field" style="left:243px;top:332px;width:111px;height:21px;font-size:6px">First Name:</div>
  <div class="field" style="left:361px;top:332px;width:111px;height:21px;font-size:6px">Last Name:</div>
  <div class="field" style="left:479px;top:332px;width:112px;height:21px;font-size:6px">Country:</div>
  <div class="field" style="left:243px;top:358px;width:111px;height:21px;font-size:6px">Email:</div>
  <div class="field" style="left:361px;top:358px;width:111px;height:21px;font-size:6px">Confirm Email:</div>
  <div class="field" style="left:479px;top:358px;width:112px;height:21px;font-size:6px">Phone:</div>
  <div class="field field--area" style="left:243px;top:386px;width:348px;height:70px;font-size:6px">Message:</div>
  <div class="check" style="left:244px;top:464px;width:8px;height:8px"></div>
  <div class="optin" style="left:258px;top:464px;font-size:5.5px">I would like to subscribe to your newsletter.</div>
  <div class="verify" style="left:243px;top:483px;width:98px;height:25px">
    <div class="check" style="left:6px;top:8px;width:9px;height:9px"></div>
    <div style="left:20px;top:9px;font-size:4.5px;color:#444">I'm not a robot</div>
  </div>
  <div class="send" style="left:243px;top:520px;width:56px;height:21px;font-size:5.5px">SEND</div>

  <div class="map" role="img" aria-label="Street map of the office surroundings with a pin on the office address" style="left:0;top:571px;width:652px;height:267px"></div>

  <footer class="footer" style="left:0;top:838px;width:652px;height:177px">
    <div class="brand" style="left:60px;top:68px;font-size:13px"><span class="mark" style="width:13px;height:13px"></span>StayNest</div>
    <div class="f-head" style="left:182px;top:28px;font-size:9px">Quick Links</div>
    <div class="f-list" style="left:182px;top:49px;font-size:6px;gap:8px"><span>Home</span><span>Search</span><span>Property</span><span>Custom</span><span>Contact Us</span></div>
    <div class="f-head" style="left:285px;top:28px;font-size:9px">Company</div>
    <div class="f-list" style="left:285px;top:49px;font-size:6px;gap:8px"><span>Privacy Policies</span><span>Reservation Policies</span><span>Cookie Policy</span></div>
    <div class="f-head" style="left:394px;top:28px;font-size:9px">Contact Us</div>
    <div class="f-row" style="left:394px;top:49px;font-size:6px"><svg width="5" height="7" viewBox="0 0 10 13"><path d="M5 0a5 5 0 0 1 5 5c0 3.5-5 8-5 8S0 8.5 0 5a5 5 0 0 1 5-5z" fill="#fff"/></svg><span>Via degli Orti 7 50100<br>Valdarno, Toscana (Italy)</span></div>
    <div class="f-row" style="left:394px;top:80px;font-size:6px"><svg width="5" height="6" viewBox="0 0 10 10"><path d="M2 0l2 2.5-1.2 1.3a6 6 0 0 0 3.4 3.4L7.5 6 10 8l-1.5 2C4 10 0 6 0 1.5z" fill="#fff"/></svg><span>+39 055 4128370</span></div>
    <div class="f-row" style="left:394px;top:99px;font-size:6px"><svg width="6" height="5" viewBox="0 0 12 9"><rect width="12" height="9" fill="#fff"/><path d="M0 0l6 5 6-5" stroke="#1d1d1d" fill="none"/></svg><span>info@staynest.com</span></div>
    <div class="f-head" style="left:539px;top:28px;font-size:9px">Follow Us</div>
    <div class="f-row" style="left:539px;top:50px;font-size:6px;align-items:center"><span class="dot" style="width:11px;height:11px"></span><span>Friendbook</span></div>
    <div class="f-row" style="left:539px;top:68px;font-size:6px;align-items:center"><span class="dot" style="width:11px;height:11px"></span><span>Chirper</span></div>
    <div class="f-row" style="left:539px;top:86px;font-size:6px;align-items:center"><span class="dot" style="width:11px;height:11px"></span><span>Snapgram</span></div>
    <div class="copy" style="left:0;top:139px;font-size:5.5px">Copyright © 2021 <b>StayNest</b>. All rights reserved.</div>
  </footer>
</section>

<!-- Mobile page -->
<section class="page mob" aria-label="Contact page, mobile layout">
  <div class="brand" style="left:56px;top:9px;font-size:15px"><span class="mark" style="width:15px;height:15px"></span>StayNest</div>
  <div class="topbar" style="left:0;top:36px;width:214px;height:28px;padding-left:0;justify-content:space-between;padding:0 8px">
    <span><svg width="18" height="11" viewBox="0 0 18 11" style="position:static;display:block"><rect width="18" height="1.6" fill="#fff"/><rect y="4.7" width="18" height="1.6" fill="#fff"/><rect y="9.4" width="18" height="1.6" fill="#fff"/></svg></span>
    <span style="font-size:8px">&#9786; &nbsp;&#9825; &nbsp;EN &#709;</span>
  </div>
  <div class="hero" role="img" aria-label="Photo of an arcaded shopping street with lanterns" style="left:0;top:64px;width:214px;height:51px"></div>
  <div class="hero-title" style="left:0;top:85px;font-size:7.5px">CONTACT US</div>

  <div class="crumb" style="left:0;top:123px;width:214px;text-align:center;font-size:8px">Home &nbsp;/&nbsp; <b>Contact us</b></div>
  <div class="h1" style="left:5px;top:146px;font-size:14px">Contact Us</div>
  <p class="lead" style="left:5px;top:168px;width:206px;font-size:6.5px">Use this form to contact us regarding any topics other than specific property requests which should be done using the form on the property detail pages.</p>
  <div class="h2" style="left:5px;top:218px;font-size:10.5px">StayNest</div>
  <div class="info" style="left:5px;top:246px;font-size:6.5px">
    <svg width="7" height="9" viewBox="0 0 10 13"><path d="M5 0a5 5 0 0 1 5 5c0 3.5-5 8-5 8S0 8.5 0 5a5 5 0 0 1 5-5z" fill="#14b57e"/><circle cx="5" cy="5" r="1.8" fill="#fff"/></svg>
    <span>Via degli Orti 7 50100 Valdarno<br>Toscana, Italy</span>
  </div>
  <div class="info" style="left:5px;top:292px;font-size:6.5px"><svg width="7" height="8" viewBox="0 0 10 10"><path d="M2 0l2 2.5-1.2 1.3a6 6 0 0 0 3.4 3.4L7.5 6 10 8l-1.5 2C4 10 0 6 0 1.5z" fill="#14b57e"/></svg><span>Phone: +39 055 4128370</span></div>
  <div class="info" style="left:5px;top:326px;font-size:6.5px"><svg width="7" height="8" viewBox="0 0 10 10"><rect x="0" y="3" width="10" height="7" fill="#14b57e"/><rect x="2" y="0" width="6" height="4" fill="#14b57e"/></svg><span>Fax: +39 055 4128371</span></div>
  <div class="info" style="left:5px;top:359px;font-size:6.5px"><svg width="7" height="8" viewBox="0 0 10 10"><circle cx="5" cy="5" r="4.5" fill="#14b57e"/></svg><span>VAT Code: IT04217650392</span></div>

  <div class="field" style="left:5px;top:388px;width:204px;height:31px;font-size:7px">First Name:</div>
  <div class="field" style="left:5px;top:422px;width:204px;height:31px;font-size:7px">Last Name:</div>
  <div class="field" style="left:5px;top:456px;width:204px;height:31px;font-size:7px">Email:</div>
  <div class="field" style="left:5px;top:490px;width:204px;height:31px;font-size:7px">Confirm Email:</div>
  <div class="field" style="left:5px;top:524px;width:204px;height:31px;font-size:7px">Phone:</div>
  <div class="field" style="left:5px;top:558px;width:204px;height:31px;font-size:7px">Country:</div>
  <div class="field field--area" style="left:5px;top:592px;width:204px;height:106px;font-size:7px">Message:</div>
  <div class="check" style="left:6px;top:709px;width:10px;height:10px"></div>
  <div class="optin" style="left:24px;top:709px;font-size:6.5px">I would like to subscribe to your newsletter.</div>
  <div class="verify" style="left:5px;top:734px;width:137px;height:35px">
    <div class="check" style="left:7px;top:11px;width:12px;height:12px"></div>
    <div style="left:25px;top:13px;font-size:5.5px;color:#444">I'm not a robot</div>
  </div>
  <div class="send" style="left:5px;top:780px;width:58px;height:22px;font-size:6px">SEND</div>

  <div class="map" role="img" aria-label="Street map of the office surroundings with a pin on the office address" style="left:0;top:825px;width:214px;height:166px"></div>

  <footer class="footer" style="left:0;top:991px;width:214px;height:599px">
    <div class="f-head" style="left:5px;top:17px;font-size:11px">Quick Links</div>
    <div class="f-list" style="left:5px;top:47px;font-size:8px;gap:11px"><span>Home</span><span>Search</span><span>Property</span><span>Custom</span><span>Contact Us</span></div>
    <div class="f-head" style="left:5px;top:164px;font-size:11px">Company</div>
    <div class="f-list" style="left:5px;top:194px;font-size:8px;gap:11px"><span>Privacy Policies</span><span>Reservation Policies</span><span>Cookie Policy</span></div>
    <div class="f-head" style="left:5px;top:267px;font-size:11px">Contact Us</div>
    <div class="f-row" style="left:5px;top:298px;font-size:8px"><svg width="7" height="9" viewBox="0 0 10 13"><path d="M5 0a5 5 0 0 1 5 5c0 3.5-5 8-5 8S0 8.5 0 5a5 5 0 0 1 5-5z" fill="#fff"/></svg><span>Via degli Orti 7 50100<br>Valdarno, Toscana (Italy)</span></div>
    <div class="f-row" style="left:5px;top:339px;font-size:8px"><svg width="7" height="8" viewBox="0 0 10 10"><path d="M2 0l2 2.5-1.2 1.3a6 6 0 0 0 3.4 3.4L7.5 6 10 8l-1.5 2C4 10 0 6 0 1.5z" fill="#fff"/></svg><span>+39 055 4128370</span></div>
    <div class="f-row" style="left:5px;top:367px;font-size:8px"><svg width="8" height="6" viewBox="0 0 12 9" style="margin-top:2px"><rect width="12" height="9" fill="#fff"/><path d="M0 0l6 5 6-5" stroke="#1d1d1d" fill="none"/></svg><span>info@staynest.com</span></div>
    <div class="f-head" style="left:5px;top:404px;font-size:11px">Follow Us</div>
    <div class="f-row" style="left:5px;top:439px;font-size:8px;align-items:center;gap:7px"><span class="dot" style="width:16px;height:16px"></span><span>Friendbook</span></div>
    <div class="f-row" style="left:5px;top:466px;font-size:8px;align-items:center;gap:7px"><span class="dot" style="width:16px;height:16px"></span><span>Chirper</span></div>
    <div class="f-row" style="left:5px;top:492px;font-size:8px;align-items:center;gap:7px"><span class="dot" style="width:16px;height:16px"></span><span>Snapgram</span></div>
    <div class="brand" style="left:60px;top:552px;font-size:13px"><span class="mark" style="width:13px;height:13px"></span>StayNest</div>
    <div class="copy" style="left:0;top:578px;font-size:5.5px">Copyright © 2021 <b>StayNest</b>. All rights reserved.</div>
  </footer>
</section>

</body>
</html>
```